Flowmark Engineering Business Card

our company has just rebranded and taken on a new logo design. We now need to update our business cards with the new logo. This is also an opportunity to reformat and modernize our look. We are an engineering company so the look needs to be formal and professional yet it should look modern. Have a look at our current card and the new card should have the same information.

Target Market(s)

Engineering firms, government, mining companies

Industry/Entity Type

Mechanical Engineering

Contact Information for Business Card

see example attached

Requirements
Must have
• look professional and modern
Should not have
• should not include the office locations 'Brisbane, Sydney and Kuala Lumpur'
• you will find this on the example but it should not be included in these versions. please remove from your submissions and resubmit

```html
<!DOCTYPE html>
<html lang="en">
<head>
<meta charset="utf-8">
<title>Flowmark Engineering – Business Card</title>
<link href="https://fonts.googleapis.com/css2?family=Exo+2:wght@400;500;600&display=swap" rel="stylesheet">
<style>
  :root {
    --backdrop: #e9eaeb;
    --card: #ffffff;
    --card-shade: #f1f2f3;
    --teal-deep: #0d4053;
    --teal-mid: #2f6d80;
    --teal-light: #7fa7b4;
    --silver: #cfd7db;
    --silver-soft: #e6eaec;
    --brand-blue: #3b41a3;
    --name-teal: #1d5f72;
    --text-grey: #4a5257;
  }
  * { box-sizing: border-box; margin: 0; padding: 0; }
  html, body {
    width: 1200px; height: 828px; overflow: hidden;
    background: var(--backdrop);
    font-family: "Exo 2", "Segoe UI", sans-serif;
  }
  .canvas {
    width: 1200px; height: 828px;
    display: flex; align-items: center; justify-content: center; gap: 50px;
  }
  .card {
    position: relative;
    width: 540px; height: 309px;
    background: linear-gradient(135deg, var(--card) 40%, var(--card-shade));
    box-shadow: 0 6px 18px rgba(0,0,0,0.14);
    overflow: hidden;
  }
  .card-art { position: absolute; inset: 0; width: 100%; height: 100%; }

  .brand {
    position: absolute;
    display: flex; align-items: center; gap: 12px;
    color: var(--brand-blue);
    font-weight: 600;
  }
  .brand-dot {
    width: 40px; height: 40px; border-radius: 50%;
    border: 3px solid var(--brand-blue);
  }
  .brand-name { display: flex; flex-direction: column; line-height: 1; letter-spacing: 1px; }
  .brand-name .primary { font-size: 30px; text-transform: uppercase; }
  .brand-name .secondary { font-size: 13px; text-transform: uppercase; letter-spacing: 6px; margin-top: 4px; }

  .card-front .brand { left: 34px; bottom: 46px; }

  .card-back .brand { left: 238px; bottom: 30px; }
  .card-back .brand-dot { width: 34px; height: 34px; }
  .card-back .brand-name .primary { font-size: 26px; }
  .card-back .brand-name .secondary { font-size: 11px; letter-spacing: 5px; }

  .person {
    position: absolute; right: 28px; top: 26px; text-align: right;
    color: var(--name-teal); text-transform: uppercase;
  }
  .person-name { font-size: 19px; font-weight: 500; letter-spacing: 1.5px; }
  .person-role { font-size: 12px; letter-spacing: 2px; color: var(--text-grey); margin-top: 2px; }

  .address {
    position: absolute; right: 28px; top: 92px; text-align: right;
    font-size: 12px; line-height: 1.45; color: var(--text-grey);
  }
  .contacts {
    position: absolute; right: 28px; top: 140px; list-style: none;
    font-size: 10.5px; line-height: 1.75; color: var(--text-grey); text-align: right;
  }
  .contacts li { display: flex; align-items: center; justify-content: flex-end; gap: 6px; }
  .contacts svg { width: 10px; height: 10px; fill: none; stroke: var(--teal-mid); stroke-width: 1.6; }
</style>
</head>
<body>
<main class="canvas">

  <section class="card card-front" aria-label="Card front">
    <svg class="card-art" viewBox="0 0 540 309" preserveAspectRatio="none" aria-hidden="true">
      <defs>
        <linearGradient id="front-swoosh" x1="0" y1="0" x2="1" y2="0">
          <stop offset="0" stop-color="#ffffff" stop-opacity="0"/>
          <stop offset="0.55" stop-color="#c3ccd1"/>
          <stop offset="1" stop-color="#8fa5ae"/>
        </linearGradient>
      </defs>
      <path d="M300 0 C 360 20, 420 30, 540 95 L540 0 Z" fill="var(--silver-soft)"/>
      <path d="M310 0 C 380 30, 440 40, 540 90 L540 78 C 450 40, 390 18, 340 0 Z" fill="url(#front-swoosh)"/>
      <path d="M318 0 C 350 8, 365 14, 380 22 C 360 12, 340 6, 330 0 Z" fill="var(--teal-deep)"/>
      <path d="M420 36 C 470 50, 510 66, 540 86 L540 92 C 505 72, 465 56, 420 36 Z" fill="var(--teal-mid)"/>
    </svg>
    <div class="brand">
      <span class="brand-dot"></span>
      <span class="brand-name"><span class="primary">Flowmark</span><span class="secondary">Engineering</span></span>
    </div>
  </section>

  <section class="card card-back" aria-label="Card back">
    <svg class="card-art" viewBox="0 0 540 309" preserveAspectRatio="none" aria-hidden="true">
      <defs>
        <linearGradient id="back-teal" x1="0" y1="1" x2="1" y2="0">
          <stop offset="0" stop-color="var(--teal-deep)"/>
          <stop offset="0.7" stop-color="var(--teal-mid)"/>
          <stop offset="1" stop-color="var(--teal-light)"/>
        </linearGradient>
        <linearGradient id="back-silver" x1="0" y1="0" x2="1" y2="0">
          <stop offset="0" stop-color="#aebcc3"/>
          <stop offset="1" stop-color="#ffffff" stop-opacity="0"/>
        </linearGradient>
      </defs>
      <path d="M0 0 H250 C 225 70, 160 110, 175 190 C 185 250, 215 280, 220 309 H0 Z" fill="url(#back-teal)"/>
      <path d="M250 0 H275 C 245 75, 185 115, 195 190 C 203 250, 232 285, 236 309 H220 C 215 280, 185 250, 175 190 C 160 110, 225 70, 250 0 Z" fill="url(#back-silver)"/>
      <path d="M262 0 H268 C 240 75, 178 115, 188 190 C 196 250, 226 285, 230 309 H226 C 221 283, 191 250, 182 190 C 170 115, 234 72, 262 0 Z" fill="var(--teal-deep)"/>
    </svg>

    <div class="person">
      <p class="person-name">Daniel Reeve</p>
      <p class="person-role">Director</p>
    </div>
    <p class="address">417 12th Floor Quay<br>Harbour Road NTH</p>
    <ul class="contacts">
      <li>020 481 7350
        <svg viewBox="0 0 10 10"><path d="M2 1 L4 3 L3 4 C3.5 5.5 4.5 6.5 6 7 L7 6 L9 8 L8 9 C4 9 1 6 1 2 Z"/></svg></li>
      <li>020 481 7350
        <svg viewBox="0 0 10 10"><rect x="2.5" y="0.8" width="5" height="8.4" rx="1"/></svg></li>
      <li>020 481 7350
        <svg viewBox="0 0 10 10"><rect x="1" y="4" width="8" height="4.5"/><rect x="2.5" y="1" width="5" height="3"/></svg></li>
      <li>hello@flowmarkeng.com
        <svg viewBox="0 0 10 10"><rect x="0.8" y="2" width="8.4" height="6"/><path d="M1 2.3 L5 5.5 L9 2.3"/></svg></li>
      <li>www.flowmarkeng.com
        <svg viewBox="0 0 10 10"><circle cx="5" cy="5" r="4"/><path d="M1 5 H9 M5 1 C3 3.5 3 6.5 5 9 M5 1 C7 3.5 7 6.5 5 9"/></svg></li>
    </ul>

    <div class="brand">
      <span class="brand-dot"></span>
      <span class="brand-name"><span class="primary">Flowmark</span><span class="secondary">Engineering</span></span>
    </div>
  </section>

</main>
</body>
</html>
```